Website for Apartment Rental in Prague

I would like to create designs of my website focused on luxury apartment rentals in Prague, Czech Republic. I created initial mock-ups, They are all attached. I need to design homepage and subpage. The mock-ups were created by combining elements from different websites that I liked but I need you to create a design that is unique and original. The attached files a only a guidance for the structure of the website but not for the design. Try to be creative.

Apartment

```html
<!DOCTYPE html>
<html lang="en">
<head>
<meta charset="utf-8">
<title>Belle Nuit Apartment Prague</title>
<link href="https://fonts.googleapis.com/css2?family=Cormorant+Garamond:wght@500;600&family=Figtree:wght@400;500;600;700&family=Jost:ital,wght@0,400;0,500;1,400&display=swap" rel="stylesheet">
<style>
:root{
  --accent:#f5ab00;
  --ink:#111111;
  --text:#2a2a2a;
  --muted:#666666;
  --line:#d8d8d8;
  --band:#ececec;
  --white:#ffffff;
  --footer:#141414;
}
*{box-sizing:border-box;margin:0;padding:0}
html,body{width:1200px;height:2293px;overflow:hidden;background:var(--white)}
body{position:relative;font-family:"Figtree",Arial,sans-serif;color:var(--text)}
.abs{position:absolute}

/* hero */
.hero{left:0;top:0;width:1200px;height:628px;
  background:
   radial-gradient(ellipse at 30% 45%,rgba(230,200,150,.55),transparent 45%),
   radial-gradient(ellipse at 85% 40%,rgba(60,90,150,.6),transparent 50%),
   linear-gradient(180deg,#2a3450 0%,#4a4234 40%,#7a5a36 70%,#3c2818 100%)}
.hero-top{left:0;top:0;width:1200px;height:145px;background:linear-gradient(180deg,rgba(10,12,20,.75),rgba(10,12,20,.25))}
.topline{left:0;top:77px;width:1200px;height:1px;background:rgba(255,255,255,.25)}
.lang{left:142px;top:34px;width:37px;height:19px;border:1px solid #fff;color:#fff;font-size:12px;font-weight:600;display:flex;align-items:center;justify-content:center;gap:3px}
.toplink{color:#fff;font-size:12.5px;font-weight:500;top:36px}
.brand{left:480px;top:18px;width:240px;text-align:center;color:#fff;font-family:"Jost",sans-serif;font-weight:500;font-size:17px;line-height:21px}
.contact{color:#fff;font-size:12.5px;top:36px;display:flex;align-items:center;gap:7px}
.nav{left:142px;top:88px;width:916px;display:flex;justify-content:space-between;color:#fff;font-size:12.5px;font-weight:600}
.hero-title{left:0;top:335px;width:1200px;text-align:center;color:#fff;font-family:"Cormorant Garamond",serif;font-weight:600;font-size:44px;letter-spacing:4px;text-shadow:0 2px 6px rgba(0,0,0,.5)}
.dots{left:578px;top:601px;display:flex;gap:4px}
.dots i{width:9px;height:9px;border-radius:50%;border:1px solid #fff;display:block}
.dots i.on{background:#fff}

/* booking */
.book-title{left:0;top:686px;width:1200px;text-align:center;font-size:24px;font-weight:600;color:var(--ink)}
.accent{color:var(--accent)}
.field-label{top:742px;font-size:11.5px;color:var(--text)}
.field{top:764px;height:33px;border:1px solid #c8c8c8;border-radius:3px;background:#fff;font-size:11px;color:#444;display:flex;align-items:center;justify-content:space-between;padding:0 10px}
.check-btn{left:798px;top:764px;width:127px;height:33px;background:var(--accent);border-radius:3px;color:#fff;font-size:11.5px;font-weight:600;display:flex;align-items:center;justify-content:center}

/* vision */
.vision{left:0;top:864px;width:1200px;height:501px;background:var(--band)}
.vision-title{left:0;top:918px;width:1200px;text-align:center;font-size:24px;font-weight:600;color:var(--ink)}
.vision-text{left:165px;top:968px;width:870px;text-align:center;font-family:"Jost",sans-serif;font-size:13px;line-height:20px;color:var(--text)}
.badge{left:573px;top:1027px;width:52px;height:52px;border:2px solid var(--accent);border-radius:50%;display:flex;align-items:center;justify-content:center}
.designed{left:0;top:1088px;width:1200px;text-align:center;font-size:14px;font-weight:600;line-height:19px;color:var(--ink)}
.quote{left:206px;top:1140px;width:788px;height:166px}
.quote-text{left:282px;top:1174px;width:640px;text-align:center;font-family:"Jost",sans-serif;font-style:italic;font-size:13px;line-height:22px;color:var(--text)}

/* cards */
.card{width:288px;height:361px;border:1px solid #dcdcdc;border-radius:3px;background:#fff;box-shadow:0 1px 3px rgba(0,0,0,.08)}
.card .photo{position:absolute;left:4px;top:4px;width:278px;height:171px}
.price{position:absolute;left:-6px;top:18px;height:20px;padding:0 9px;background:var(--accent);color:#fff;font-size:10.5px;font-weight:600;display:flex;align-items:center}
.card h3{position:absolute;left:15px;top:188px;width:260px;font-size:13px;line-height:17px;font-weight:700;color:var(--ink)}
.card p{position:absolute;left:15px;top:226px;width:255px;font-size:12.5px;line-height:16px;color:var(--text)}
.feats{position:absolute;left:15px;top:286px;display:flex;gap:20px;font-size:12.5px;color:var(--ink)}
.feats span{display:flex;align-items:center;gap:6px}
.card hr{position:absolute;left:4px;top:320px;width:278px;border:0;border-top:1px solid #e2e2e2}
.details{position:absolute;left:17px;top:333px;font-size:12.5px;font-weight:600;color:var(--ink)}
.book-now{position:absolute;left:184px;top:326px;width:87px;height:26px;border:2px solid var(--accent);border-radius:2px;font-size:12.5px;font-weight:600;color:var(--ink);display:flex;align-items:center;justify-content:center}

.info{left:770px;top:1821px;width:288px;height:361px;border:1px solid #dcdcdc;background:#fff;box-shadow:0 1px 3px rgba(0,0,0,.08)}
.info-head{position:absolute;left:0;top:0;width:286px;height:55px;background:var(--accent);color:#fff;font-size:22px;font-weight:600;display:flex;align-items:center;justify-content:center}
.info-block{position:absolute;left:15px;width:256px;text-align:center;font-size:12px;line-height:17px;color:var(--text)}
.info-block b{display:block;font-size:14px;font-weight:700;color:var(--ink);margin-bottom:6px}
.info-rule{position:absolute;left:15px;width:256px;border-top:1px solid #dcdcdc}

/* footer */
.footer{left:0;top:2247px;width:1200px;height:46px;background:var(--footer)}
.copy{left:142px;top:2262px;color:#ddd;font-size:11px}
.social{left:697px;top:2256px;display:flex;gap:6px}
.social i{width:24px;height:24px;border-radius:50%;display:block}
.chat{left:836px;top:2240px;width:222px;height:44px;background:var(--accent);color:#fff;font-size:15px;font-weight:600;display:flex;align-items:center;justify-content:center;gap:8px}
</style>
</head>
<body>

<div class="abs hero" role="img" aria-label="Photo of a bright luxury apartment living room with a bed, sofa and large windows over Prague at dusk"></div>
<div class="abs hero-top"></div>
<div class="abs topline"></div>

<div class="abs lang">EN <svg width="7" height="5" viewBox="0 0 7 5"><path d="M0 0h7L3.5 5z" fill="#fff"/></svg></div>
<div class="abs toplink" style="left:212px">Our Hospitality</div>
<div class="abs toplink" style="left:332px;display:flex;align-items:center;gap:7px">
  <svg width="14" height="14" viewBox="0 0 14 14"><path d="M2 1v13" stroke="#fff" stroke-width="1.5"/><path d="M2.8 1.5h9l-2 3 2 3h-9z" fill="#fff"/></svg>Discover Prague</div>
<div class="abs brand">Belle Nuit<br>Apartment Prague</div>
<div class="abs contact" style="left:726px">
  <svg width="15" height="13" viewBox="0 0 15 13"><rect x="1" y="3" width="13" height="9" fill="none" stroke="#fff" stroke-width="1.3"/><path d="M1 3l6.5 5L14 3" fill="none" stroke="#fff" stroke-width="1.3"/></svg>reservation@bellenuitstay.com</div>
<div class="abs contact" style="left:938px;font-weight:600;font-size:13px">
  <svg width="13" height="13" viewBox="0 0 24 24"><path d="M6.6 10.8a15 15 0 006.6 6.6l2.2-2.2c.3-.3.7-.4 1-.2 1.1.4 2.3.6 3.6.6.6 0 1 .4 1 1V20c0 .6-.4 1-1 1A17 17 0 013 4c0-.6.4-1 1-1h3.5c.6 0 1 .4 1 1 0 1.3.2 2.5.6 3.6.1.3 0 .7-.2 1z" fill="#fff"/></svg>420 555 018 204</div>

<nav class="abs nav">
  <span>Apartments</span><span>Location</span><span>Services</span><span>Gallery</span><span>News</span><span>Exclusive Offers &amp; Tours</span><span>For Families</span><span>Contact Us</span>
</nav>

<h1 class="abs hero-title">Being Home In Prague</h1>
<div class="abs dots"><i class="on"></i><i></i><i></i><i></i></div>

<!-- booking -->
<h2 class="abs book-title">Official Site - <span class="accent">Best Price Guaranteed</span></h2>
<div class="abs field-label" style="left:142px">Check In Date</div>
<div class="abs field-label" style="left:301px">Check Out Date</div>
<div class="abs field-label" style="left:462px">Adults</div>
<div class="abs field-label" style="left:530px">Childrens</div>
<div class="abs field-label" style="left:598px">Infants</div>
<div class="abs field-label" style="left:666px">Promotional Code</div>
<div class="abs field-label" style="left:937px">OR</div>

<div class="abs field" style="left:142px;width:149px">11/19/2017
  <svg width="14" height="14" viewBox="0 0 14 14"><rect x="1" y="2.5" width="12" height="10.5" fill="none" stroke="#555" stroke-width="1.2"/><path d="M1 5.5h12M4 1v3M10 1v3" stroke="#555" stroke-width="1.2"/></svg></div>
<div class="abs field" style="left:301px;width:150px">11/21/2017
  <svg width="14" height="14" viewBox="0 0 14 14"><rect x="1" y="2.5" width="12" height="10.5" fill="none" stroke="#555" stroke-width="1.2"/><path d="M1 5.5h12M4 1v3M10 1v3" stroke="#555" stroke-width="1.2"/></svg></div>
<div class="abs field" style="left:462px;width:57px">02<svg width="10" height="6" viewBox="0 0 10 6"><path d="M1 1l4 4 4-4" fill="none" stroke="#555" stroke-width="1.3"/></svg></div>
<div class="abs field" style="left:529px;width:58px">01<svg width="10" height="6" viewBox="0 0 10 6"><path d="M1 1l4 4 4-4" fill="none" stroke="#555" stroke-width="1.3"/></svg></div>
<div class="abs field" style="left:598px;width:57px">00<svg width="10" height="6" viewBox="0 0 10 6"><path d="M1 1l4 4 4-4" fill="none" stroke="#555" stroke-width="1.3"/></svg></div>
<div class="abs field" style="left:665px;width:123px"></div>
<div class="abs check-btn">Check Availability</div>
<div class="abs field" style="left:937px;width:121px;font-size:10px">Select Rental Unit<svg width="10" height="6" viewBox="0 0 10 6"><path d="M1 1l4 4 4-4" fill="none" stroke="#555" stroke-width="1.3"/></svg></div>

<!-- vision -->
<section class="abs vision"></section>
<h2 class="abs vision-title">A Different <span class="accent">Vision Of Travelling</span></h2>
<p class="abs vision-text">Something spectacular has arrived in the heart of Europe. Steps from Old Town, this rental experience is curated with world-class amenities, exemplary style and a level of convenience you have to experience to believe. Experience the different vision of luxury in center of Prague.</p>
<div class="abs badge">
  <svg width="24" height="24" viewBox="0 0 24 24"><rect x="5" y="3" width="14" height="6" fill="none" stroke="#f5ab00" stroke-width="1.6"/><path d="M4 12h16M6 12l12 9M18 12L6 21" stroke="#f5ab00" stroke-width="1.6"/></svg>
</div>
<div class="abs designed">Interiors Designed<br>By: <span class="accent">Belle Nuit</span></div>
<svg class="abs quote" viewBox="0 0 788 166">
  <path d="M20 26 L360 26 L378 2 L386 26 L768 18 Q776 18 775 26 L764 152 Q763 160 755 160 L14 164 Q6 164 7 156 L12 34 Q13 26 20 26z" fill="#fff"/>
</svg>
<p class="abs quote-text">Belle Nuit apartments offers short term and as well as long term options in our studio apartments and our one bedroom apartment homes. Our luxurious apartments and high quality customer service have allowed us to dominate the Prague apartment market with a proven track record. Our years of experience and knowledge have made us a premier apartment rental company as we continue to stress the importance of servicing individuals and corporations who are seeking the finest accommodations.</p>

<!-- apartment cards -->
<article class="abs card" style="left:142px;top:1431px">
  <div class="photo" role="img" aria-label="Photo of a bright kitchen and dining area with yellow flowers" style="background:linear-gradient(135deg,#d9d4cc,#f1ede6 55%,#8a6a4c)"></div>
  <div class="price">From 150 USD</div>
  <h3>Brand New Luxury Living Shinning Contemporary Design</h3>
  <p>The 22nd issue is dedicated to colors...</p>
  <div class="feats"><span><svg width="18" height="12" viewBox="0 0 18 12"><path d="M1 1v10M1 8h16v3M1 8V6h16v2M3 6V4h5v2" fill="none" stroke="#f5ab00" stroke-width="1.5"/></svg>1 Bedroom</span><span><svg width="12" height="13" viewBox="0 0 12 13"><circle cx="6" cy="3.5" r="3" fill="#f5ab00"/><path d="M0 13c0-4 2.5-6 6-6s6 2 6 6z" fill="#f5ab00"/></svg>Max 4 People</span></div>
  <hr><span class="details">Details</span><span class="book-now">Book Now</span>
</article>

<article class="abs card" style="left:456px;top:1431px">
  <div class="photo" role="img" aria-label="Photo of a grey living room with sofa and dining table" style="background:linear-gradient(135deg,#6f6f73,#c9c7c3 50%,#a58a6a)"></div>
  <div class="price">From 150 USD</div>
  <h3>Brand New Zen Luxury Living Apartment In The Center Of Prague</h3>
  <p>Recognized with Wanderlane Travelers 2017 Readers' Choice Award #1 hotel in the world...</p>
  <div class="feats"><span><svg width="18" height="12" viewBox="0 0 18 12"><path d="M1 1v10M1 8h16v3M1 8V6h16v2M3 6V4h5v2" fill="none" stroke="#f5ab00" stroke-width="1.5"/></svg>1 Bedroom</span><span><svg width="12" height="13" viewBox="0 0 12 13"><circle cx="6" cy="3.5" r="3" fill="#f5ab00"/><path d="M0 13c0-4 2.5-6 6-6s6 2 6 6z" fill="#f5ab00"/></svg>Max 4 People</span></div>
  <hr><span class="details">Details</span><span class="book-now">Book Now</span>
</article>

<article class="abs card" style="left:770px;top:1431px">
  <div class="photo" role="img" aria-label="Photo of a wooden kitchen with a set dining table" style="background:linear-gradient(135deg,#b9c0c6,#8a6136 55%,#5a4030)"></div>
  <div class="price">From 150 USD</div>
  <h3>Expedition Prague! Top Loca" Brand New Apartment</h3>
  <p>for your managementcommittee, showroomsession, incentive trip, product launch, privatization...</p>
  <div class="feats"><span><svg width="18" height="12" viewBox="0 0 18 12"><path d="M1 1v10M1 8h16v3M1 8V6h16v2M3 6V4h5v2" fill="none" stroke="#f5ab00" stroke-width="1.5"/></svg>1 Bedroom</span><span><svg width="12" height="13" viewBox="0 0 12 13"><circle cx="6" cy="3.5" r="3" fill="#f5ab00"/><path d="M0 13c0-4 2.5-6 6-6s6 2 6 6z" fill="#f5ab00"/></svg>Max 4 People</span></div>
  <hr><span class="details">Details</span><span class="book-now">Book Now</span>
</article>

<article class="abs card" style="left:142px;top:1821px">
  <div class="photo" role="img" aria-label="Photo of a warm living room with a red sofa and wooden floor" style="background:linear-gradient(135deg,#d8c7a8,#e8dcc6 50%,#b26a40)"></div>
  <div class="price">From 150 USD</div>
  <h3>Brand New Zen Luxury Living Apartment In The Center Of Prague</h3>
  <p>The 22nd issue is dedicated to colors...</p>
  <div class="feats"><span><svg width="18" height="12" viewBox="0 0 18 12"><path d="M1 1v10M1 8h16v3M1 8V6h16v2M3 6V4h5v2" fill="none" stroke="#f5ab00" stroke-width="1.5"/></svg>1 Bedroom</span><span><svg width="12" height="13" viewBox="0 0 12 13"><circle cx="6" cy="3.5" r="3" fill="#f5ab00"/><path d="M0 13c0-4 2.5-6 6-6s6 2 6 6z" fill="#f5ab00"/></svg>Max 4 People</span></div>
  <hr><span class="details">Details</span><span class="book-now">Book Now</span>
</article>

<article class="abs card" style="left:456px;top:1821px">
  <div class="photo" role="img" aria-label="Photo of a white bedroom and living area with a blue rug" style="background:linear-gradient(135deg,#e6e4e0,#f4f2ee 55%,#9aa8b4)"></div>
  <div class="price">From 150 USD</div>
  <h3>Brand New Modern Apartment Unbeatable Location</h3>
  <p>Recognized with Wanderlane Travelers 2017</p>
  <div class="feats"><span><svg width="18" height="12" viewBox="0 0 18 12"><path d="M1 1v10M1 8h16v3M1 8V6h16v2M3 6V4h5v2" fill="none" stroke="#f5ab00" stroke-width="1.5"/></svg>1 Bedroom</span><span><svg width="12" height="13" viewBox="0 0 12 13"><circle cx="6" cy="3.5" r="3" fill="#f5ab00"/><path d="M0 13c0-4 2.5-6 6-6s6 2 6 6z" fill="#f5ab00"/></svg>Max 4 People</span></div>
  <hr><span class="details">Details</span><span class="book-now">Book Now</span>
</article>

<aside class="abs info">
  <div class="info-head">Need To Know</div>
  <div class="info-block" style="top:75px"><b>APARTMENTS</b>Also Avaliable To Rent All The Apartments Together For Companies Or Larger Groups,</div>
  <div class="info-rule" style="top:155px"></div>
  <div class="info-block" style="top:178px"><b>CHECK-OUT</b>12 Noon; Earliest Check-in, 3PM- Both Are Flexible, By Arragement.</div>
  <div class="info-rule" style="top:257px"></div>
  <div class="info-block" style="top:279px"><b>RATES</b>Prices From 150 USD Per Night Including Tax</div>
</aside>

<!-- footer -->
<footer class="abs footer"></footer>
<div class="abs copy">Copyright © 2017 Belle Nuit Apartment Prague. All Rights Reserved.</div>
<div class="abs social"><i style="background:#3b5a9a"></i><i style="background:#2fa4e7"></i><i style="background:#0a77b5"></i><i style="background:#d6443a"></i></div>
<div class="abs chat">
  <svg width="18" height="16" viewBox="0 0 18 16"><path d="M9 1C4.6 1 1 3.8 1 7.2c0 1.9 1.1 3.6 2.9 4.7L3 15l3.6-2.2c.8.2 1.6.3 2.4.3 4.4 0 8-2.8 8-6.2S13.4 1 9 1z" fill="#fff"/><circle cx="5.5" cy="7.2" r="1" fill="#f5ab00"/><circle cx="9" cy="7.2" r="1" fill="#f5ab00"/><circle cx="12.5" cy="7.2" r="1" fill="#f5ab00"/></svg>
  Please Leave a Message</div>

</body>
</html>
```